CalmPeak Nurses' Manifesto

Design a manifesto to inspire and motivate nurses to work at minimum standards of excellence in their nursing practice.

The manifesto will become a feature of our website, at conferences, workshops and retreats. It will also be featured on other marketing tools.

Primary Market:
Nurses and/or other healthcare professionals (specifically Doctors, Occupational Therapists, Psychologists and Social Workers).

However the manifesto is equally applicable to all nurses and healthcare professionals from new graduates to very experienced senior clinicians, administration officers,managers and healthcare executive personnel.

Mainly females and primarily 35 to 65 years old, which suggests people in this target age group have extensive experience, but have become jaded'.

The purpose of our business is to assist healthcare professionals, primarily nurses, to maintain their enthusiasm and excellence in service provision, for their benefit as well as the benefit of the clients.

I have attached:
File 1: Copy Samples and examples: which has the copy for the manifesto, examples that appeal to us and our 3 attempts.
File 2: Our colour Spec Sheet, HOWEVER the colours are not necessary limited to these colours. These colours are not in the logo that will be on the manifesto. The colours on the logo attached can/or also be used.
File 3: Prototype logo. The final logo will be available within 3 to 4 days.

Industry/Entity Type

Healthcare

Requirements
Must have
• Must use the copy as per the attached file.

It should be contemporary, eye catching and motivational.

Should not have
• MUST BE EASY TO READ. Each line MUST be clearly defined from each other.

```html
<!DOCTYPE html>
<html lang="en">
<head>
<meta charset="utf-8">
<title>CalmPeak – A Nurses' Manifesto</title>
<link rel="stylesheet" href="https://fonts.googleapis.com/css2?family=Alfa+Slab+One&family=Anton&family=Oswald:wght@700&display=swap">
<style>
  :root {
    --ink: #231f20;
    --orange: #f7862a;
    --teal: #5ec6c0;
    --paper-light: #ffffff;
    --paper-edge: #d6d6d6;
  }
  html, body {
    margin: 0;
    padding: 0;
    width: 849px;
    height: 1200px;
    overflow: hidden;
    background: var(--paper-edge);
  }
  .manifesto {
    display: block;
    width: 849px;
    height: 1200px;
  }
  .slab { font-family: "Alfa Slab One", Georgia, serif; }
  .condensed { font-family: "Anton", "Arial Narrow", sans-serif; }
  .title { font-family: "Oswald", "Arial Narrow", sans-serif; font-weight: 700; }
  .ink { fill: var(--ink); }
  .orange { fill: var(--orange); }
  .teal { fill: var(--teal); }
  .feature { filter: drop-shadow(1px 2px 1px rgba(0,0,0,0.25)); }
</style>
</head>
<body>
<svg class="manifesto" viewBox="0 0 849 1200" xmlns="http://www.w3.org/2000/svg" role="img" aria-label="A Nurses' Manifesto by CalmPeak">
  <defs>
    <radialGradient id="paper" cx="50%" cy="50%" r="70%">
      <stop offset="0%" stop-color="#ffffff"/>
      <stop offset="60%" stop-color="#f3f3f3"/>
      <stop offset="100%" stop-color="#d6d6d6"/>
    </radialGradient>
  </defs>
  <rect class="backdrop" width="849" height="1200" fill="url(#paper)"/>

  <g class="heading">
    <text class="title ink" x="385" y="78" font-size="40" textLength="415" lengthAdjust="spacingAndGlyphs">A Nurses' Manifesto</text>
    <text class="slab teal feature" x="47" y="155" font-size="72" textLength="321" lengthAdjust="spacingAndGlyphs">NURSE</text>
  </g>

  <g class="line-self-care slab orange">
    <text x="388" y="114" font-size="24" textLength="164" lengthAdjust="spacingAndGlyphs">LOOK AFTER</text>
    <text x="388" y="173" font-size="54" textLength="252" lengthAdjust="spacingAndGlyphs">YOURSELF</text>
    <text x="662" y="172" font-size="24" textLength="110" lengthAdjust="spacingAndGlyphs">&amp; VALUE</text>
    <text x="388" y="208" font-size="23" textLength="404" lengthAdjust="spacingAndGlyphs">YOUR HEALTH AS MUCH AS YOU</text>
    <text x="388" y="240" font-size="23" textLength="415" lengthAdjust="spacingAndGlyphs">VALUE THE HEALTH OF OTHERS.</text>
  </g>

  <g class="line-open slab ink">
    <text x="47" y="200" font-size="21" textLength="172" lengthAdjust="spacingAndGlyphs">WITH OPEN</text>
    <text x="227" y="200" font-size="32" textLength="140" lengthAdjust="spacingAndGlyphs">HANDS,</text>
    <text x="47" y="240" font-size="32" textLength="152" lengthAdjust="spacingAndGlyphs">HEARTS</text>
    <text x="206" y="240" font-size="21" textLength="20" lengthAdjust="spacingAndGlyphs">&amp;</text>
    <text x="234" y="240" font-size="32" textLength="133" lengthAdjust="spacingAndGlyphs">MINDS</text>
  </g>

  <g class="line-delight slab ink">
    <text x="47" y="275" font-size="18" textLength="308" lengthAdjust="spacingAndGlyphs">DELIGHT YOUR CLIENTS &amp;</text>
    <text x="47" y="300" font-size="18" textLength="370" lengthAdjust="spacingAndGlyphs">COLLEAGUES BY EXCEEDING THEIR</text>
    <text x="425" y="300" font-size="62" textLength="375" lengthAdjust="spacingAndGlyphs">EXPECTATIONS</text>
  </g>

  <text class="slab orange" x="47" y="346" font-size="50" textLength="753" lengthAdjust="spacingAndGlyphs">DELIVER CARE SKILLFULLY.</text>

  <g class="line-respect slab ink">
    <text x="47" y="398" font-size="46" textLength="219" lengthAdjust="spacingAndGlyphs">RESPECT</text>
    <text x="275" y="398" font-size="15" textLength="147" lengthAdjust="spacingAndGlyphs">THE LIMITS OF</text>
    <text x="47" y="418" font-size="15" textLength="358" lengthAdjust="spacingAndGlyphs">PEOPLE'S KNOWLEDGE &amp; SHARE YOUR</text>
    <text x="47" y="438" font-size="15" textLength="254" lengthAdjust="spacingAndGlyphs">KNOWLEDGE GENEROUSLY.</text>
  </g>

  <g class="line-support condensed ink">
    <text x="433" y="405" font-size="48" textLength="173" lengthAdjust="spacingAndGlyphs">SUPPORT</text>
    <text x="622" y="383" font-size="20" textLength="178" lengthAdjust="spacingAndGlyphs">YOUR COLLEAGUES</text>
    <text x="433" y="435" font-size="20" textLength="181" lengthAdjust="spacingAndGlyphs">&amp; CHAMPION THEIR</text>
    <text x="620" y="436" font-size="46" textLength="183" lengthAdjust="spacingAndGlyphs">PURPOSE.</text>
  </g>

  <text class="slab orange" x="47" y="475" font-size="38" textLength="753" lengthAdjust="spacingAndGlyphs">LEARN SOMETHING NEW EACH DAY.</text>
  <text class="slab ink" x="47" y="502" font-size="16" textLength="753" lengthAdjust="spacingAndGlyphs">TRUST YOUR KNOWLEDGE &amp; SEEK ADVICE ONLY FROM RESPECTED SOURCES.</text>
  <text class="slab orange" x="47" y="552" font-size="52" textLength="756" lengthAdjust="spacingAndGlyphs">BE A LIFELONG LEARNER.</text>
  <text class="slab ink" x="47" y="602" font-size="50" textLength="756" lengthAdjust="spacingAndGlyphs">CELEBRATE, RESPECT &amp; VALUE</text>
  <text class="slab orange" x="47" y="637" font-size="34" textLength="756" lengthAdjust="spacingAndGlyphs">THE DIVERSITY OF AUSTRALIAN CULTURE.</text>

  <g class="line-smile slab ink">
    <text x="47" y="686" font-size="50" textLength="143" lengthAdjust="spacingAndGlyphs">SMILE</text>
    <text x="197" y="663" font-size="15" textLength="250" lengthAdjust="spacingAndGlyphs">&amp; INFECT OTHERS WITH</text>
    <text x="300" y="680" font-size="15" textLength="45" lengthAdjust="spacingAndGlyphs">YOUR</text>
    <text x="47" y="712" font-size="28" textLength="401" lengthAdjust="spacingAndGlyphs">HAPPINESS &amp; HAVE FUN!</text>
  </g>

  <g class="line-right slab ink">
    <text x="466" y="664" font-size="15" textLength="168" lengthAdjust="spacingAndGlyphs">ALWAYS DO THE</text>
    <text x="640" y="687" font-size="48" textLength="163" lengthAdjust="spacingAndGlyphs">RIGHT</text>
    <text x="468" y="708" font-size="48" textLength="159" lengthAdjust="spacingAndGlyphs">THING</text>
    <text x="632" y="711" font-size="14" textLength="171" lengthAdjust="spacingAndGlyphs">WITHOUT EXCEPTION.</text>
  </g>

  <g class="line-unique slab orange">
    <text x="47" y="747" font-size="17" textLength="211" lengthAdjust="spacingAndGlyphs">YOU ARE UNIQUE,</text>
    <text x="72" y="766" font-size="17" textLength="186" lengthAdjust="spacingAndGlyphs">REVEL IN YOUR</text>
    <text x="264" y="766" font-size="40" textLength="221" lengthAdjust="spacingAndGlyphs">INDIVIDUALITY.</text>
    <text x="493" y="741" font-size="14" textLength="84" lengthAdjust="spacingAndGlyphs">ALWAYS BE</text>
    <text x="493" y="761" font-size="14" textLength="77" lengthAdjust="spacingAndGlyphs">FOCUSED.</text>
    <text x="578" y="763" font-size="44" textLength="225" lengthAdjust="spacingAndGlyphs">SOLUTION</text>
  </g>

  <text class="slab ink" x="47" y="805" font-size="40" textLength="756" lengthAdjust="spacingAndGlyphs">SEEK SUCCESS FIRSTLY FROM WITHIN.</text>

  <g class="line-lead slab">
    <text class="ink" x="47" y="837" font-size="16" textLength="376" lengthAdjust="spacingAndGlyphs">ONLY FOLLOW EXCEPTIONAL LEADERS.</text>
    <text class="orange" x="47" y="863" font-size="16" textLength="456" lengthAdjust="spacingAndGlyphs">IF THERE IS NO ONE LEFT TO FOLLOW, THEN LEAD!</text>
    <text class="ink" x="562" y="832" font-size="17" textLength="238" lengthAdjust="spacingAndGlyphs">ALWAYS LEAD WITH</text>
    <text class="ink" x="562" y="854" font-size="17" textLength="238" lengthAdjust="spacingAndGlyphs">PURPOSE, PASSION</text>
    <text class="ink" x="562" y="876" font-size="17" textLength="214" lengthAdjust="spacingAndGlyphs">&amp; COMMITMENT.</text>
  </g>

  <g class="line-practice slab ink">
    <text x="47" y="894" font-size="15" textLength="409" lengthAdjust="spacingAndGlyphs">RESPOND TO COMPLEX SITUATIONS INNOVATIVELY,</text>
    <text x="47" y="916" font-size="15" textLength="409" lengthAdjust="spacingAndGlyphs">CREATIVELY &amp; SAFELY WITHIN THE SCOPE OF</text>
    <text x="465" y="918" font-size="38" textLength="338" lengthAdjust="spacingAndGlyphs">YOUR PRACTICE.</text>
  </g>

  <g class="line-can-do slab orange">
    <text x="47" y="962" font-size="15" textLength="83" lengthAdjust="spacingAndGlyphs">ADOPT A</text>
    <text x="135" y="965" font-size="44" textLength="210" lengthAdjust="spacingAndGlyphs">'CAN DO'</text>
    <text x="47" y="986" font-size="19" textLength="298" lengthAdjust="spacingAndGlyphs">ATTITUDE TO EVERYTHING</text>
    <text x="47" y="1008" font-size="19" textLength="263" lengthAdjust="spacingAndGlyphs">THAT COMES YOUR WAY.</text>
  </g>

  <g class="line-thoughts slab ink">
    <text x="367" y="948" font-size="25" textLength="433" lengthAdjust="spacingAndGlyphs">CHOOSE YOUR THOUGHTS WISELY,</text>
    <text x="367" y="982" font-size="27" textLength="433" lengthAdjust="spacingAndGlyphs">THEY CREATE YOUR REALITY.</text>
  </g>

  <text class="slab teal feature" x="333" y="1055" font-size="56" textLength="470" lengthAdjust="spacingAndGlyphs">LIVE YOUR DREAM.</text>

  <g class="brand">
    <circle cx="102" cy="1102" r="11" fill="var(--teal)"/>
    <text class="slab orange" x="120" y="1111" font-size="24">CalmPeak</text>
  </g>
</svg>
</body>
</html>
```